Candle Rental Business seeks new website design

We need a new website design for a Candle hire business. The business rents out pillar candles for events such as weddings and corporate events. Our main target market is weddings. The business name is Hire a Lantern. The business name does not have a logo design.

We would like a website that is light in colours and creates a warm atmosphere. The design needs to be elegant and upmarket. There are different size candles that we hire out, ranging from 10cm diameter to 20cm diameter, flat, tall etc. All our candles are white in colour. Its just the size that differs.

We would also like to include a section for hiring out decor such as glassvases, candlebras, overlays and chairs sachets, chair covers. However, this is not the businesses main focus but an additional offering to customers.

Target Market(s)

Wedding venues and brides. Corporate events. School dances.

Industry/Entity Type

Hospitality

Logo Text

Hire a Lantern

Number of Pages Required

1 page

Font styles to use
Sans Serif
Script

Requirements
Must have
• Pictures of pillar candles. Plain white candles. The website must centre around candles.
Nice to have
• Different examples of candle centrepieces
Should not have
• Pictures must not be of brides. Pictures of surrounding is perferable.

```html
<!DOCTYPE html>
<html lang="en">
<head>
<meta charset="utf-8">
<title>Hire a Lantern</title>
<link href="https://fonts.googleapis.com/css2?family=Lato:ital,wght@0,400;0,700;1,400&family=Questrial&display=swap" rel="stylesheet">
<style>
:root{
  --pink:#cf6f9c;
  --pink-light:#f2a7c8;
  --purple:#a57cc4;
  --purple-deep:#9068b3;
  --ink:#1e1e1e;
  --text:#3a3a3a;
  --muted:#8a8a8a;
  --footer:#2b2b2b;
  --footer-line:#444;
  --white:#ffffff;
  --hero-dark:#1a110b;
  --hero-warm:#6b3f1c;
}
*{margin:0;padding:0;box-sizing:border-box}
html,body{width:1200px;height:2651px;overflow:hidden}
body{position:relative;background:var(--white);font-family:'Lato',sans-serif;color:var(--text)}
.abs{position:absolute}

/* hero */
.hero{left:0;top:0;width:1200px;height:655px;background:radial-gradient(ellipse at 55% 45%,#a86a2c 0%,var(--hero-warm) 25%,#3a2210 55%,var(--hero-dark) 100%)}
.topbar{left:0;top:0;width:1200px;height:6px;background:#111}
.brand{left:130px;top:32px;font-family:'Questrial',sans-serif;font-size:36px;color:var(--white);display:flex;align-items:center;gap:12px}
.brand-mark{width:34px;height:34px;border-radius:50%;background:var(--white)}
.phone{right:70px;top:18px;color:var(--pink-light);font-size:17px;display:flex;align-items:center;gap:8px}
.phone-dot{width:24px;height:24px;border-radius:50%;background:var(--pink);display:flex;align-items:center;justify-content:center}
.nav{left:496px;top:58px;display:flex;font-size:14px;color:var(--white)}
.nav span{margin-right:37px;position:relative}
.nav .active::after{content:"";position:absolute;left:0;right:0;bottom:-8px;height:3px;background:var(--white)}
.hero-arrow{top:290px}
.hero-caption{left:0;top:590px;width:1200px;height:65px;background:rgba(0,0,0,.45);display:flex;align-items:center;justify-content:center;font-family:'Questrial',sans-serif;color:var(--white);font-size:30px;letter-spacing:.5px}

/* service tiles */
.tile{top:693px;width:267px;height:134px;border-radius:4px;background:linear-gradient(135deg,#4a4a52,#7c6a74 55%,#3c3c42);box-shadow:0 10px 16px -8px rgba(0,0,0,.35)}
.tile-title{position:absolute;left:112px;top:20px;color:var(--white);font-family:'Questrial',sans-serif;font-size:20px;line-height:23px}
.tile-btn{position:absolute;left:112px;top:78px;border:1px solid var(--white);color:var(--white);font-size:13px;font-weight:700;padding:5px 14px}

/* welcome */
.welcome-title{left:131px;top:885px;font-family:'Questrial',sans-serif;font-weight:400;font-size:29px;color:var(--ink)}
.welcome-title b{font-weight:700;font-family:'Lato',sans-serif}
.welcome-rule{left:131px;top:931px;width:533px;height:1px;background:#ccc}
.welcome-rule::before{content:"";position:absolute;left:0;top:-1px;width:108px;height:3px;background:var(--pink)}
.welcome-copy{left:131px;top:946px;width:535px;font-size:13px;line-height:19px;color:var(--text)}
.btn-pink{left:131px;top:1085px;width:113px;height:37px;background:var(--pink);color:var(--white);font-size:14px;font-weight:700;display:flex;align-items:center;justify-content:center}
.video{left:739px;top:901px;width:330px;height:219px;background:linear-gradient(160deg,#6a6c78,#3c3e48 50%,#23252c);border-radius:2px}
.video-play{position:absolute;left:141px;top:67px;width:48px;height:48px;border-radius:50%;background:rgba(0,0,0,.45);border:2px solid rgba(255,255,255,.8);display:flex;align-items:center;justify-content:center}
.video-bar{position:absolute;left:0;bottom:0;width:100%;height:30px;background:#111}

/* decor band */
.decor{left:0;top:1179px;width:1200px;height:311px;background:radial-gradient(circle at 20% 30%,#b28fcf,var(--purple) 40%,var(--purple-deep))}
.decor-title{left:0;top:1218px;width:1200px;text-align:center;font-family:'Questrial',sans-serif;font-weight:400;font-size:28px;color:var(--white)}
.decor-title b{font-family:'Lato',sans-serif;font-weight:700}
.decor-rule{left:480px;top:1266px;width:386px;height:1px;background:rgba(255,255,255,.7)}
.decor-item{top:1312px;width:200px;text-align:center;color:var(--white);font-size:18px;font-weight:700}
.decor-ring{width:76px;height:76px;margin:0 auto 26px;border:3px solid var(--white);border-radius:50%;display:flex;align-items:center;justify-content:center}
.decor-ring.on{background:var(--pink-light)}
.decor-sep{top:1310px;width:1px;height:125px;background:rgba(255,255,255,.35)}

/* testimonials */
.section-title{left:0;top:1544px;width:1200px;text-align:center;font-family:'Questrial',sans-serif;font-weight:400;font-size:29px;color:var(--ink)}
.section-title b{font-family:'Lato',sans-serif;font-weight:700}
.section-rule{left:431px;top:1594px;width:386px;height:1px;background:#ddd}
.section-rule::before{content:"";position:absolute;left:104px;top:-1px;width:127px;height:3px;background:var(--pink)}
.quote{top:1626px;width:470px}
.avatar{width:92px;height:92px;border-radius:50%;border:4px solid var(--pink);background:linear-gradient(#a9c3d6,#6a8aa4)}
.quote-name{position:absolute;left:117px;top:24px;color:#2a3a5a;font-weight:700;font-size:14px}
.quote-role{position:absolute;left:117px;top:44px;color:var(--purple);font-size:12px}
.quote-text{position:absolute;left:0;top:105px;width:470px;font-style:italic;font-size:13px;line-height:26px;color:var(--text);text-indent:26px}
.quote-mark{position:absolute;font-family:Georgia,serif;font-size:44px;color:#b8b8b8;line-height:1}
.quote-sep{left:598px;top:1630px;width:1px;height:200px;background:#ddd}
.dots{left:555px;top:1868px;display:flex;gap:11px}
.dots span{width:15px;height:15px;border-radius:50%;background:#222}
.dots span.ring{background:var(--white);border:2px solid #222}

/* promo band */
.promo{left:0;top:1949px;width:1200px;height:375px;background:linear-gradient(90deg,#bdb7ae 0%,#7d776e 25%,#3f3c39 55%,#2c2a2a 100%)}
.promo-text{left:511px;top:2018px;width:600px;color:var(--white)}
.promo-h{font-family:'Lato',sans-serif;font-weight:700;font-size:26px;letter-spacing:.8px}
.promo-sub{font-size:21px;line-height:30px}
.promo-size{margin-top:14px;font-weight:700;font-size:18px;line-height:26px}
.btn-ghost{display:inline-flex;margin-top:18px;border:2px solid var(--white);padding:11px 26px;font-size:17px;font-weight:700;letter-spacing:.5px}

/* footer */
.footer{left:0;top:2325px;width:1200px;height:326px;background:linear-gradient(#333,var(--footer))}
.footer-line{left:0;top:2385px;width:1200px;height:1px;background:var(--footer-line)}
.footer-bottom-line{left:0;top:2600px;width:1200px;height:1px;background:var(--footer-line)}
.f-head{top:2347px;color:#e6e6e6;font-family:'Questrial',sans-serif;font-size:17px}
.f-links{left:134px;top:2400px;list-style:none;color:#ddd;font-size:12px}
.f-links li{height:30px}
.f-links li::before{content:"›";margin-right:12px;color:#999}
.news{left:306px;width:250px;color:#ddd;font-size:12px;line-height:15px}
.news-date{position:absolute;left:0;top:2px;width:22px;height:28px;border:1px solid #bbb;font-size:10px;text-align:center;line-height:13px;font-weight:700}
.news-date small{display:block;font-size:6px;line-height:8px;background:#bbb;color:#222}
.news-body{margin-left:32px}
.news-body b{color:var(--purple)}
.contact{left:602px;top:2400px;color:#ddd;font-size:12px;line-height:16px}
.contact-row{display:flex;align-items:center;gap:10px;margin-top:18px}
.field{left:848px;width:220px;height:30px;border:1px solid #555;background:#262626;color:#888;font-size:11px;padding:8px}
.btn-submit{left:848px;top:2553px;width:98px;height:30px;background:var(--purple);color:var(--white);font-weight:700;font-size:13px;display:flex;align-items:center;justify-content:center}
.copyright{left:130px;top:2617px;color:#ccc;font-size:12px}
.social{top:2614px;width:22px;height:22px;background:#ddd;border-radius:2px}
.social.first{background:var(--purple)}
</style>
</head>
<body>

<header>
  <div class="abs hero" role="img" aria-label="Candle-lit round banquet table set with glasses and white pillar candles"></div>
  <div class="abs topbar"></div>
  <div class="abs brand"><span class="brand-mark"></span>Hire a Lantern</div>
  <div class="abs phone">
    <span class="phone-dot"><svg width="12" height="12" viewBox="0 0 24 24"><path fill="#fff" d="M6.6 10.8a15 15 0 0 0 6.6 6.6l2.2-2.2c.3-.3.7-.4 1-.2 1.1.4 2.3.6 3.6.6.6 0 1 .4 1 1V20c0 .6-.4 1-1 1A17 17 0 0 1 3 4c0-.6.4-1 1-1h3.5c.6 0 1 .4 1 1 0 1.3.2 2.5.6 3.6.1.3 0 .7-.2 1z"/></svg></span>
    (123)5550-194
  </div>
  <nav class="abs nav">
    <span class="active">Home</span><span>About Us</span><span>Our Products</span><span>Hire Candles</span><span>Décor Hire</span><span>Contact Us</span>
  </nav>
  <svg class="abs hero-arrow" style="left:58px" width="30" height="80" viewBox="0 0 30 80"><polyline points="26,2 4,40 26,78" fill="none" stroke="#fff" stroke-width="2"/></svg>
  <svg class="abs hero-arrow" style="left:1112px" width="30" height="80" viewBox="0 0 30 80"><polyline points="4,2 26,40 4,78" fill="none" stroke="#fff" stroke-width="2"/></svg>
  <div class="abs hero-caption">Creating A Warm Atmosphere &amp; Special Touch To All Occasions</div>
</header>

<section class="services">
  <div class="abs tile" style="left:159px" role="img" aria-label="Softly blurred candle light">
    <div class="tile-title">Hire<br>Candles</div><div class="tile-btn">Read More</div>
  </div>
  <div class="abs tile" style="left:467px" role="img" aria-label="Softly blurred candle light">
    <div class="tile-title">Personalised<br>Candles</div><div class="tile-btn">Read More</div>
  </div>
  <div class="abs tile" style="left:772px" role="img" aria-label="Softly blurred candle light">
    <div class="tile-title">Décor<br>Hire</div><div class="tile-btn">Read More</div>
  </div>
</section>

<section class="welcome">
  <h1 class="abs welcome-title">Welcome to <b>HIRE A LANTERN</b></h1>
  <div class="abs welcome-rule"></div>
  <p class="abs welcome-copy">Lorem ipsum dolor sit amet, consectetur adipiscing elit. Nulla in sollicitudin velit, bibendum velit. Cras vel facilisis ipsum, et venenatis risus. In egestas nunc etvb eros auctor sollicitu Etiam ut enim vitae magna volutpat venenatis vitae nonprof diam. Nam nunc velit, tristique a sapien euismod, pulvinar vestibulum dui. Morbi porttitor eu erat imperdiet pretium consequat fcilelis. Cras vel facilisis ipsum, et venenatis risus. In egestas nunc etvb eros auctor sollicitu.</p>
  <div class="abs btn-pink">READ MORE</div>
  <div class="abs video" role="img" aria-label="Video of white pillar candles on a table">
    <div class="video-play"><svg width="16" height="18" viewBox="0 0 16 18"><polygon points="2,1 2,17 15,9" fill="#fff"/></svg></div>
    <div class="video-bar">
      <svg width="330" height="30" viewBox="0 0 330 30"><polygon points="14,10 14,20 22,15" fill="#ccc"/><rect x="60" y="13" width="170" height="4" rx="2" fill="#555"/><rect x="60" y="13" width="85" height="4" rx="2" fill="#cf6f9c"/></svg>
    </div>
  </div>
</section>

<section>
  <div class="abs decor" role="img" aria-label="Soft purple background with light bokeh circles"></div>
  <h2 class="abs decor-title">Our Decor <b>Hires</b></h2>
  <div class="abs decor-rule"></div>
  <div class="abs decor-item" style="left:151px"><div class="decor-ring"><svg width="30" height="40" viewBox="0 0 30 40"><path d="M10 2h10l-2 10 6 26H6l6-26z" fill="none" stroke="#fff" stroke-width="2.5"/></svg></div>Glass Vases</div>
  <div class="abs decor-sep" style="left:385px"></div>
  <div class="abs decor-item" style="left:395px"><div class="decor-ring on"><svg width="40" height="40" viewBox="0 0 40 40"><path d="M6 18h28M20 18v16M12 38h16M6 10v8M20 6v12M34 10v8" stroke="#fff" stroke-width="3" fill="none"/></svg></div>Candle Bars</div>
  <div class="abs decor-sep" style="left:609px"></div>
  <div class="abs decor-item" style="left:633px"><div class="decor-ring"><svg width="28" height="40" viewBox="0 0 28 40"><path d="M6 22V6a8 8 0 0 1 16 0v16M4 22h20v4H4zM6 26v12M22 26v12" stroke="#fff" stroke-width="2.5" fill="none"/></svg></div>Chair Sachets</div>
  <div class="abs decor-sep" style="left:846px"></div>
  <div class="abs decor-item" style="left:842px"><div class="decor-ring"><svg width="42" height="32" viewBox="0 0 42 32"><path d="M8 14V6h26v8M3 14h36v10H3zM6 24v6M36 24v6" stroke="#fff" stroke-width="2.5" fill="none"/></svg></div>Chair Covers</div>
</section>

<section>
  <h2 class="abs section-title">Client <b>Testimonials</b></h2>
  <div class="abs section-rule"></div>
  <div class="abs quote" style="left:131px">
    <div class="avatar" role="img" aria-label="Client portrait"></div>
    <div class="quote-name">Mr. Rowan Ellery</div><div class="quote-role">Lorem Ipsum</div>
    <span class="quote-mark" style="left:0;top:102px">“</span>
    <p class="quote-text">Utm tellus dolor, dapibus eget, elemen velmki cursus eleifelita arnean auctorbni wisi et urnam. Lorem ipsum dolor sit amet, conse ctetur adipiscing elit. Nulla in sollicitudin velit, bibendum velit.Cras vel facilisis ipsum, et venenatis risus.</p>
    <span class="quote-mark" style="right:0;top:180px">”</span>
  </div>
  <div class="abs quote-sep"></div>
  <div class="abs quote" style="left:636px">
    <div class="avatar" role="img" aria-label="Client portrait"></div>
    <div class="quote-name">Mr. Rowan Ellery</div><div class="quote-role">Lorem Ipsum</div>
    <span class="quote-mark" style="left:0;top:102px">“</span>
    <p class="quote-text">Utm tellus dolor, dapibus eget, elemen velmki cursus eleifelita arnean auctorbni wisi et urnam. Lorem ipsum dolor sit amet, conse ctetur adipiscing elit. Nulla in sollicitudin velit, bibendum velit.Cras vel facilisis ipsum, et venenatis risus.</p>
    <span class="quote-mark" style="right:0;top:180px">”</span>
  </div>
  <div class="abs dots"><span></span><span class="ring"></span><span></span><span></span></div>
</section>

<section>
  <div class="abs promo" role="img" aria-label="White pillar candle in a beaded holder among silver festive decorations"></div>
  <div class="abs promo-text">
    <div class="promo-h">We DESIGN, MANUFACTURE &amp; PERSONALISE</div>
    <div class="promo-sub">All Of Our CANDLES In Our Most Distinctive Handcrafted Manner!</div>
    <div class="promo-size">Different Size Candles Ranging From<br>10cm Diameter To 20cm Diameter, Flat, Tall Etc</div>
    <div class="btn-ghost">BUY NOW</div>
  </div>
</section>

<footer>
  <div class="abs footer"></div>
  <div class="abs footer-line"></div>
  <div class="abs footer-bottom-line"></div>
  <div class="abs f-head" style="left:134px">Quick Links</div>
  <div class="abs f-head" style="left:306px">News / Updates</div>
  <div class="abs f-head" style="left:602px">Contact Detail</div>
  <div class="abs f-head" style="left:848px">Quick Contact</div>
  <ul class="abs f-links"><li>Home</li><li>About Us</li><li>Our Products</li><li>Hire Candles</li><li>Décor Hire</li><li>Contact Us</li></ul>
  <div class="abs news" style="top:2400px"><div class="news-date">22<small>MAR</small></div><div class="news-body"><b>Duis autem vel eumsodn</b><br>Lorem ipsum dolor sit ametn nk consectetuer adipiscing elit.</div></div>
  <div class="abs news" style="top:2464px"><div class="news-date">22<small>MAR</small></div><div class="news-body"><b>Duis autem vel eumsodn</b><br>Lorem ipsum dolor sit ametn nk consectetuer adipiscing elit.</div></div>
  <div class="abs news" style="top:2528px"><div class="news-date">22<small>MAR</small></div><div class="news-body"><b>Duis autem vel eumsodn</b><br>Lorem ipsum dolor sit ametn nk consectetuer adipiscing elit.</div></div>
  <div class="abs contact">
    <b>Hire a Lantern</b><br>16 Lorem ipsum dolor sit sed<br>benetion, Street no-123456
    <div class="contact-row"><svg width="12" height="12" viewBox="0 0 24 24"><path fill="#bbb" d="M6.6 10.8a15 15 0 0 0 6.6 6.6l2.2-2.2c.3-.3.7-.4 1-.2 1.1.4 2.3.6 3.6.6.6 0 1 .4 1 1V20c0 .6-.4 1-1 1A17 17 0 0 1 3 4c0-.6.4-1 1-1h3.5c.6 0 1 .4 1 1 0 1.3.2 2.5.6 3.6.1.3 0 .7-.2 1z"/></svg>123-555-0142</div>
    <div class="contact-row"><svg width="13" height="12" viewBox="0 0 26 24"><rect x="6" y="2" width="14" height="6" fill="#bbb"/><rect x="2" y="9" width="22" height="9" rx="2" fill="#bbb"/><rect x="6" y="15" width="14" height="7" fill="#bbb"/></svg>123-555-0178</div>
    <div class="contact-row"><svg width="13" height="10" viewBox="0 0 26 20"><rect x="1" y="1" width="24" height="18" fill="none" stroke="#bbb" stroke-width="2"/><polyline points="1,1 13,11 25,1" fill="none" stroke="#bbb" stroke-width="2"/></svg>info@hirealantern.com</div>
  </div>
  <div class="abs field" style="top:2404px">Name</div>
  <div class="abs field" style="top:2440px">Email</div>
  <div class="abs field" style="top:2476px;height:68px">Message</div>
  <div class="abs btn-submit">SUBMIT</div>
  <div class="abs copyright">Copyright © 2016 HIRE A LANTERN | All Rights Reserved.</div>
  <div class="abs social first" style="left:954px"></div>
  <div class="abs social" style="left:981px"></div>
  <div class="abs social" style="left:1008px"></div>
  <div class="abs social" style="left:1035px"></div>
</footer>

</body>
</html>
```